Free Legal Consultation

Bram,

I am wondering if you could take the Open House invitation you created for me for KDRF and use it to create a postcard for people stopping in to let us know if they are interested in making a meeting with us.
So, front of the card - left side of the card, we would have the front door picture, then on the right side of the card,we would have the logo, underneath a picture of me,

then two locations:
742 Corley Ave., Newton, MA
8 Tobermay Ave., Norwell, MA
(617) 482-3061.

On the back of the card, on the left side of the card 3 check boxes next to 3 categories:
Estate Planning
Estate and Trust Administration
Elder Law and Nursing Care Planning

On the right side of the card:

I am interested in a free legal consultation:

Name: ______________________________
Address: ____________________________
____________________________
Phone: ____________________________
Email: ____________________________

Can you work up a design for me?

It would be great to have it for the open house.

Thanks, Marla

```html
<!DOCTYPE html>
<html lang="en">
<head>
<meta charset="utf-8">
<title>Free Legal Consultation – Postcard Back</title>
<link rel="stylesheet" href="https://fonts.googleapis.com/css2?family=Open+Sans:wdth,wght@75..100,400..700&display=swap">
<style>
  :root {
    --band: #231f20;
    --paper: #e6e6e7;
    --pill: #6d6e70;
    --box: #ffffff;
    --box-edge: #6d6e70;
    --ink: #231f20;
    --rule: #555557;
  }
  html, body {
    margin: 0;
    padding: 0;
    width: 1200px;
    height: 929px;
    overflow: hidden;
    background: var(--paper);
  }
  .postcard {
    position: relative;
    width: 1200px;
    height: 929px;
    background: var(--paper);
    font-family: "Open Sans", Arial, sans-serif;
    font-stretch: 75%;
    color: var(--ink);
  }
  .band {
    position: absolute;
    left: 0;
    width: 1200px;
    background: var(--band);
  }
  .band--top { top: 0; height: 89px; }
  .band--bottom { bottom: 0; height: 89px; }

  .services {
    position: absolute;
    left: 74px;
    top: 265px;
    margin: 0;
    padding: 0;
    list-style: none;
  }
  .service {
    display: flex;
    align-items: stretch;
    height: 116px;
    margin-bottom: 56px;
  }
  .service__check {
    width: 66px;
    background: var(--box);
    border: 3px solid var(--box-edge);
    border-right: none;
    border-radius: 22px 0 0 22px;
  }
  .service__label {
    width: 387px;
    margin-left: 0;
    background: var(--pill);
    border-radius: 22px;
    color: #fff;
    display: flex;
    align-items: center;
    justify-content: center;
    text-align: center;
    font-size: 30px;
    font-weight: 400;
    line-height: 1.05;
    text-transform: uppercase;
    letter-spacing: 0.2px;
  }

  .request {
    position: absolute;
    left: 575px;
    top: 280px;
    width: 560px;
  }
  .request__title {
    margin: 0 0 40px;
    font-size: 30px;
    font-weight: 700;
    letter-spacing: -0.2px;
  }
  .field {
    display: flex;
    align-items: baseline;
    height: 75px;
    font-size: 21px;
    font-weight: 700;
  }
  .field__label { margin-right: 14px; }
  .field__line {
    flex: 1;
    border-bottom: 3px dotted var(--rule);
    transform: translateY(-4px);
  }
  .field--blank .field__line { margin-left: 0; }
</style>
</head>
<body>
<main class="postcard">
  <div class="band band--top"></div>

  <ul class="services">
    <li class="service">
      <span class="service__check"></span>
      <span class="service__label">Estate Planning</span>
    </li>
    <li class="service">
      <span class="service__check"></span>
      <span class="service__label">Estate and Trust<br>Administration</span>
    </li>
    <li class="service">
      <span class="service__check"></span>
      <span class="service__label">Elder Law and Nursing<br>Care Planning</span>
    </li>
  </ul>

  <section class="request">
    <h2 class="request__title">I am interested in a free legal consultation:</h2>
    <div class="field"><span class="field__label">Name:</span><span class="field__line"></span></div>
    <div class="field"><span class="field__label">Address:</span><span class="field__line"></span></div>
    <div class="field field--blank"><span class="field__line"></span></div>
    <div class="field"><span class="field__label">Phone:</span><span class="field__line"></span></div>
    <div class="field"><span class="field__label">Email:</span><span class="field__line"></span></div>
  </section>

  <div class="band band--bottom"></div>
</main>
</body>
</html>
```